whitening syringe artwork design

3ml syringe with silkscreen printing:
sample:
https://www.quorvashop.example/Velvo-Crane-Whitening-Syringes-Carbamide/dp/Q51842KX93/ref=sr_1_6?crid=7ZP42WQ81LMRT&dchild=1&keywords=whitening+syringes&qid=1698802214&sprefix=whitening+sy%2Caps%2C150&sr=8-6
inside the writing:
"teeth whitening gel " change to "Orvanne WHITENING GEL"
"Advanced formula" change to our logo and "Not all gels are created equal. "

additional requirements:
Inches: 2.01" wide x 1.34" around

CM: 5.1cm wide x 3.4cm around

See attached template: Generic_Syringe Labels 3ml_Silkscreen.pdf

- Leave the volume gage where it is, so it prints correctly on the syringe

- Feel free to change the color and font style

- An "identifying marker" is required: Teeth Whitening Syringe or Teeth Whitening Gel (for example)

- Replace "Teeth Whitening Gel - Advanced Formula" with your text and logo - it is there as a placeholder

-We require PDF files created to print ready specifications. Color images should be down-sampled to 300DPI

-Please provide us your Tintora color references for the color used in your artwork

https://www.tintora.example/color-finder#/pick?tintoraBook=tintoraSolidCoatedV3M2

-Please ensure that all fonts are embedded in the PDF document or make sure you convert fonts to outlines to prevent any issues with fonts (AI-Type-Create Outlines)

We will need your print ready artwork in a high resolution PDF file

teeth whitening ecommerce

• follow the guide document, and add text I want, color code from Tintora is provided

```html
<!DOCTYPE html>
<html lang="en">
<head>
<meta charset="utf-8">
<title>Syringe Silkscreen Artwork – Sola Whitening</title>
<link rel="stylesheet" href="https://fonts.googleapis.com/css2?family=Nunito:ital,wght@1,800&family=Montserrat:wght@700&family=Roboto+Condensed:wght@700&display=swap">
<style>
  :root {
    --paper: #ffffff;
    --navy: #2b2870;
    --navy-deep: #2a2660;
    --navy-bright: #2f2d86;
    --silver-light: #f2f2f2;
    --silver-mid: #c9c9c9;
    --silver-dark: #9a9a9a;
    --gauge-dark: #25346e;
    --gauge-blue: #2a70b9;
    --label-white: #f7f7f7;
  }
  html, body {
    margin: 0;
    padding: 0;
    width: 1200px;
    height: 718px;
    overflow: hidden;
    background: var(--paper);
  }
  .artboard { display: block; width: 1200px; height: 718px; }
  .banner-title {
    font-family: "Nunito", "Arial Rounded MT Bold", sans-serif;
    font-style: italic;
    font-weight: 800;
    fill: var(--label-white);
  }
  .brand-name {
    font-family: "Montserrat", "Helvetica Neue", sans-serif;
    font-weight: 700;
    fill: var(--navy);
    letter-spacing: 4px;
  }
  .brand-mark { fill: var(--navy); }
  .tagline {
    font-family: "Montserrat", "Helvetica Neue", sans-serif;
    font-weight: 700;
    fill: var(--navy);
    font-size: 12px;
  }
  .gauge-mark { stroke: url(#gauge-ink); stroke-width: 3; }
  .gauge-number {
    font-family: "Roboto Condensed", "Arial Narrow", sans-serif;
    font-weight: 700;
    fill: var(--gauge-dark);
    font-size: 26px;
  }
  .gauge-unit {
    font-family: "Roboto Condensed", "Arial Narrow", sans-serif;
    font-weight: 700;
    fill: var(--gauge-dark);
    font-size: 20px;
  }
</style>
</head>
<body>
<svg class="artboard" viewBox="0 0 1200 718" xmlns="http://www.w3.org/2000/svg">
  <defs>
    <linearGradient id="silver-frame" x1="0" y1="0" x2="0" y2="1">
      <stop offset="0" stop-color="var(--silver-dark)"/>
      <stop offset="0.3" stop-color="var(--silver-light)"/>
      <stop offset="0.7" stop-color="var(--silver-mid)"/>
      <stop offset="1" stop-color="var(--silver-dark)"/>
    </linearGradient>
    <linearGradient id="label-fill" x1="0" y1="0" x2="0" y2="1">
      <stop offset="0" stop-color="var(--navy-bright)"/>
      <stop offset="1" stop-color="var(--navy-deep)"/>
    </linearGradient>
    <linearGradient id="gauge-ink" gradientUnits="userSpaceOnUse" x1="650" y1="0" x2="1110" y2="0">
      <stop offset="0" stop-color="var(--gauge-dark)"/>
      <stop offset="1" stop-color="var(--gauge-blue)"/>
    </linearGradient>
    <g id="label-banner">
      <path d="M0 66 L36 6 Q40 0 47 0 L401 0 L367 60 Q363 66 356 66 Z" fill="url(#silver-frame)"/>
      <path d="M12 58 L40 7 L389 7 L361 54 Q359 58 354 58 Z" fill="url(#label-fill)"/>
    </g>
  </defs>

  <!-- Pen label, upper -->
  <g class="pen-label">
    <use href="#label-banner" x="131" y="184"/>
    <text class="banner-title" x="330" y="231" text-anchor="middle" font-size="35">Sola Whitening Pen</text>
    <text class="brand-name" x="312" y="280" text-anchor="middle" font-size="24">GLEAMLY</text>
    <circle class="brand-mark" cx="312" cy="298" r="10"/>
  </g>

  <!-- Pen label, lower -->
  <g class="pen-label">
    <use href="#label-banner" x="112" y="414"/>
    <text class="banner-title" x="311" y="461" text-anchor="middle" font-size="35">Sola Whitening Pen</text>
    <text class="brand-name" x="324" y="510" text-anchor="middle" font-size="24">GLEAMLY</text>
    <circle class="brand-mark" cx="324" cy="528" r="10"/>
  </g>

  <!-- Gel label -->
  <g class="gel-label">
    <use href="#label-banner" transform="translate(699 215) scale(0.978 0.97)"/>
    <text class="banner-title" x="891" y="259" text-anchor="middle" font-size="33">Teeth Whitening Gel</text>
    <text class="brand-name" x="900" y="300" text-anchor="middle" font-size="19">GLEAMLY</text>
    <circle class="brand-mark" cx="900" cy="315" r="8"/>
    <text class="tagline" x="900" y="344" text-anchor="middle">Not all gels are created equal.</text>
  </g>

  <!-- Volume gauge -->
  <g class="volume-gauge">
    <line class="gauge-mark" x1="659" y1="389" x2="659" y2="453"/>
    <line class="gauge-mark" x1="729" y1="414" x2="729" y2="453"/>
    <line class="gauge-mark" x1="798" y1="389" x2="798" y2="453"/>
    <line class="gauge-mark" x1="878" y1="414" x2="878" y2="453"/>
    <line class="gauge-mark" x1="958" y1="389" x2="958" y2="453"/>
    <line class="gauge-mark" x1="1027" y1="414" x2="1027" y2="453"/>
    <line class="gauge-mark" x1="1097" y1="389" x2="1097" y2="453"/>

    <text class="gauge-number" transform="translate(738 393) rotate(-90)">½</text>
    <text class="gauge-number" transform="translate(807 379) rotate(-90)">1</text>
    <text class="gauge-number" transform="translate(887 404) rotate(-90)">1½</text>
    <text class="gauge-number" transform="translate(967 382) rotate(-90)">2</text>
    <text class="gauge-number" transform="translate(1036 406) rotate(-90)">2½</text>
    <text class="gauge-number" transform="translate(1106 382) rotate(-90)">3</text>
    <text class="gauge-unit" transform="translate(1120 446) rotate(-90)">ml/cc</text>
  </g>
</svg>
</body>
</html>
```